Stationary Set Rebrand for Brennick

We are a Canadian Distribution and Service Company that was established in 1969. Over the past 5 decades we have expanded our business and have warehouses across Canada. We specialize in adhesive tapes, adhesives, films, safety, warehouse, shipping, janitorial and packaging supplies.

We have updated our logo design and would like a new corporate branding identity that includes a new fresh Stationary Set (Business Cards, Letterhead, Letterhead MS Word, Envelope, Presentation Folders, Email Signatures, Notepad Covers, etc.)

Target Market(s)

Industrial Business Sector

Font styles to use
Sans Serif

Colors
0054AA
0677BA
7BADD7
CADEEF
E8F1F8
0094D4
00A9DD
6FCCEA
C7EBF8
E9F6FB
00AB8E
00BBA5
67D7C9
C6EFE9
E9F9F6
EB3D1F
EC4F4E
F09395
F8D3D4
FCEDEE

Requirements
Should not have
• Colors not too light, darker colours preferred

```html
<!DOCTYPE html>
<html lang="en">
<head>
<meta charset="utf-8">
<title>Brennick Stationery Set</title>
<link href="https://fonts.googleapis.com/css2?family=Montserrat:wght@400;500;600;700;800&family=Lato:wght@400;700&display=swap" rel="stylesheet">
<style>
:root{
  --bg:#b9b9b9;
  --paper:#ffffff;
  --ink:#1f1d1e;
  --ink-soft:#5a5a5a;
  --red:#e2231a;
  --rule:#c9c9c9;
  --pattern:#2a2a2a;
  --window:#ebebeb;
}
*{box-sizing:border-box;margin:0;padding:0}
html,body{width:1200px;height:768px;overflow:hidden}
body{background:var(--bg);position:relative;font-family:"Montserrat",sans-serif;color:var(--ink)}
.piece{position:absolute;background:var(--paper);overflow:hidden}
.wordmark{font-family:"Montserrat",sans-serif;font-weight:800;color:var(--ink);letter-spacing:-.02em;line-height:1;display:flex;align-items:center;gap:.18em}
.wordmark .dot{width:.28em;height:.28em;background:var(--red);display:inline-block}
.wordmark.light{color:#fff}
.band{position:absolute;left:0;right:0;background:var(--ink);color:#fff;display:flex;align-items:center;justify-content:center}
.band::after{content:"";position:absolute;right:0;top:0;bottom:0;width:16%;background:var(--red)}
.contacts{list-style:none;border-left:1.5px solid var(--red)}
.contacts li{display:flex;align-items:center;gap:5px;color:var(--ink)}
.contacts svg{fill:var(--red);flex:none}

/* letterhead */
.letterhead{left:66px;top:74px;width:426px;height:609px}
.letterhead .wordmark{position:absolute;left:37px;top:38px;font-size:32px}
.letterhead .contacts{position:absolute;left:285px;top:33px;padding-left:7px;font-size:9px;line-height:13.3px}
.recipient{position:absolute;left:37px;top:137px}
.recipient .name{font-family:"Lato",sans-serif;font-weight:700;font-size:9px}
.recipient .role{font-family:"Lato",sans-serif;font-weight:700;font-size:6.5px;margin-top:2px}
.date{position:absolute;right:37px;top:148px;font-family:"Lato",sans-serif;font-size:6.5px;color:var(--ink-soft)}
.body-copy{position:absolute;left:37px;right:37px;top:180px;font-family:"Lato",sans-serif;font-size:6.3px;line-height:10.3px;color:var(--ink-soft);text-align:justify}
.body-copy p+p{margin-top:10.3px}
.signature{position:absolute;left:37px;top:416px;width:92px;height:22px;background:linear-gradient(90deg,#e8e8e8,#f4f4f4)}
.signer{position:absolute;left:37px;top:453px}
.signer .name{font-family:"Lato",sans-serif;font-weight:700;font-size:9px}
.signer .role{font-family:"Lato",sans-serif;font-weight:700;font-size:6.5px;color:var(--ink-soft);margin-top:3px}
.letterhead .band{top:576px;height:20px;font-size:7.5px}

/* cards */
.card{width:250px;height:146px;border-radius:8px}
.card-front{left:525px;top:74px;background:var(--ink)}
.card-front .pattern{position:absolute;inset:0;background:linear-gradient(180deg,var(--pattern),var(--ink))}
.card-front .wordmark{position:absolute;left:0;right:0;top:58px;justify-content:center;font-size:36px}
.card-back{left:525px;top:236px}
.card-back .wordmark{position:absolute;left:0;right:0;top:22px;justify-content:center;font-size:30px}
.person{position:absolute;right:130px;top:80px;text-align:right}
.person .name{font-weight:700;font-size:8.5px}
.person .role{color:var(--red);font-size:6.5px;margin-top:3px}
.card-back .contacts{position:absolute;left:128px;top:74px;padding-left:7px;font-size:6.6px;line-height:11px}
.card-back .band{top:124px;height:12px;font-size:6px}

/* envelope */
.envelope{left:800px;width:330px;height:146px}
.envelope-front{top:74px}
.envelope-front .wordmark{position:absolute;left:22px;top:18px;font-size:19px}
.envelope-front .window{position:absolute;left:21px;top:73px;width:112px;height:35px;border-radius:4px;background:var(--window)}
.envelope-front .band{top:122px;height:14px;font-size:5px;justify-content:flex-start;padding-left:22px}
.envelope-back{top:236px}

/* notebooks */
.notebook-cover{left:551px;top:418px;width:189px;height:263px;background:var(--ink)}
.notebook-cover .pattern{position:absolute;inset:0 0 40% 0;background:linear-gradient(180deg,var(--pattern),var(--ink))}
.notebook-cover .wordmark{position:absolute;left:0;right:0;top:212px;justify-content:center;font-size:23px}
.coil{position:absolute;width:12px;background:repeating-linear-gradient(180deg,#9a9a9a 0 2px,transparent 2px 11.5px)}
.coil.cover{left:546px;top:424px;height:250px}
.notebook-open{left:759px;top:416px;width:372px;height:262px;background:transparent;overflow:visible}
.page{position:absolute;top:0;width:186px;height:262px;background:var(--paper);overflow:hidden}
.page.left{left:0}.page.right{left:186px}
.page .wordmark{position:absolute;left:17px;top:14px;font-size:11px}
.page .date-line{position:absolute;right:18px;top:34px;font-size:3.5px;color:var(--ink-soft)}
.page .lines{position:absolute;left:17px;right:17px;top:45px;height:200px;background:repeating-linear-gradient(180deg,transparent 0 9.4px,var(--rule) 9.4px 10.4px)}
.page .band{top:248px;height:8px;font-size:3.2px}
.coil.open{left:180px;top:8px;height:246px}
</style>
</head>
<body>

<section class="piece letterhead">
  <div class="wordmark">Brennick<span class="dot"></span></div>
  <ul class="contacts">
    <li><svg width="8" height="8" viewBox="0 0 24 24"><path d="M6.6 10.8a15 15 0 0 0 6.6 6.6l2.2-2.2c.3-.3.7-.4 1-.2 1.1.4 2.3.6 3.6.6.6 0 1 .4 1 1V20c0 .6-.4 1-1 1A17 17 0 0 1 3 4c0-.6.4-1 1-1h3.5c.6 0 1 .4 1 1 0 1.3.2 2.5.6 3.6.1.3 0 .7-.2 1z"/></svg>548-555-0172</li>
    <li><svg width="8" height="8" viewBox="0 0 24 24"><path d="M2 5h20v14H2zM2 5l10 8 10-8" /></svg>info@brennicksales.com</li>
    <li><svg width="8" height="8" viewBox="0 0 24 24"><circle cx="12" cy="12" r="10"/></svg>www.brennicksales.com</li>
  </ul>
  <div class="recipient"><div class="name">Dear. Mrs Ellen Ward</div><div class="role">Chief Director</div></div>
  <div class="date">Date: 16-October-2025</div>
  <div class="body-copy">
    <p>Lorem ipsum dolor sit amet, consectetur adipiscing elit, sed do eiusmod tempor incididunt ut labore et dolore magna aliqua. Sollicitudin ac orci phasellus egestas tellus rutrum tellus. Euismod elementum nisi quis eleifend quam adipiscing vitae proin sagittis. Egestas sed tempus urna et pharetra pharetra. Quis blandit turpis cursus in hac habitasse. Sed velit dignissim sodales ut eu. Ac auctor augue mauris augue neque. In arcu cursus euismod quis viverra nibh cras pulvinar mattis. Libero justo laoreet sit amet. Felis eget nunc lobortis mattis aliquam faucibus purus in. Pulvinar etiam non quam lacus suspendisse faucibus. Odio tempor orci dapibus ultrices. Velit dignissim sodales ut eu sem integer vitae justo. Fermentum et sollicitudin ac orci phasellus egestas. Pharetra vel turpis nunc eget lorem dolor sed. Sed turpis tincidunt id aliquet risus feugiat in ante. Mus mauris vitae ultricies leo integer malesuada nunc vel. Rhoncus urna neque viverra justo nec ultrices dui. Ut placerat orci nulla pellentesque dignissim enim sit amet.</p>
    <p>Bibendum arcu vitae elementum curabitur vitae nunc. Nunc pulvinar sapien et ligula ullamcorper malesuada. At elementum eu facilisis sed. Erat pellentesque adipiscing commodo elit at imperdiet dui accumsan sit. Nunc scelerisque viverra mauris in aliquam sem fringilla. In vitae turpis massa sed. Volutpat ac tincidunt vitae semper quis lectus nulla at. Massa placerat duis ultricies lacus sed turpis. Dui vivamus arcu felis bibendum ut tristique et egestas. Blandit aliquam etiam erat velit scelerisque in dictum non consectetur. Id neque aliquam vestibulum morbi blandit cursus risus at. Sed egestas egestas fringilla phasellus faucibus scelerisque eleifend donec. Ornare quam viverra orci sagittis eu volutpat odio facilisis. Volutpat sed cras ornare arcu dui vivamus arcu. Interdum consectetur libero id faucibus nisl.</p>
    <p>Viverra mauris in aliquam sem. Mattis molestie a iaculis at erat pellentesque adipiscing commodo elit. Sit amet volutpat consequat mauris nunc. Aliquam nulla facilisi cras fermentum. Sed turpis tincidunt id aliquet risus feugiat. Augue neque gravida in fermentum et sollicitudin ac orci.</p>
  </div>
  <div class="signature" role="img" aria-label="Handwritten signature"></div>
  <div class="signer"><div class="name">Daniel Reeve</div><div class="role">Chief Director</div></div>
  <div class="band">27-310 Cedar Point Rd, Guelph, ON N1K 4T2</div>
</section>

<section class="piece card card-front">
  <div class="pattern" role="img" aria-label="Dark tonal repeat pattern"></div>
  <div class="wordmark light">Brennick<span class="dot"></span></div>
</section>

<section class="piece card card-back">
  <div class="wordmark">Brennick<span class="dot"></span></div>
  <div class="person"><div class="name">MARCUS ELLERY</div><div class="role">Founder &amp; CEO</div></div>
  <ul class="contacts">
    <li><svg width="6" height="6" viewBox="0 0 24 24"><path d="M6.6 10.8a15 15 0 0 0 6.6 6.6l2.2-2.2c.3-.3.7-.4 1-.2 1.1.4 2.3.6 3.6.6.6 0 1 .4 1 1V20c0 .6-.4 1-1 1A17 17 0 0 1 3 4c0-.6.4-1 1-1h3.5c.6 0 1 .4 1 1 0 1.3.2 2.5.6 3.6.1.3 0 .7-.2 1z"/></svg>548-555-0172</li>
    <li><svg width="6" height="6" viewBox="0 0 24 24"><path d="M2 5h20v14H2z"/></svg>info@brennicksales.com</li>
    <li><svg width="6" height="6" viewBox="0 0 24 24"><circle cx="12" cy="12" r="10"/></svg>www.brennicksales.com</li>
  </ul>
  <div class="band">27-310 Cedar Point Rd, Guelph, ON N1K 4T2</div>
</section>

<section class="piece envelope envelope-front">
  <div class="wordmark">Brennick<span class="dot"></span></div>
  <div class="window"></div>
  <div class="band">27-310 Cedar Point Rd, Guelph, ON N1K 4T2</div>
</section>

<section class="piece envelope envelope-back">
  <svg width="330" height="146" viewBox="0 0 330 146">
    <path d="M0 0 L155 108 Q165 115 175 108 L330 0" fill="none" stroke="#d8d8d8" stroke-width="1.2"/>
    <path d="M0 146 L92 78 M330 146 L238 78" fill="none" stroke="#e2e2e2" stroke-width="1"/>
  </svg>
</section>

<section class="piece notebook-cover">
  <div class="pattern" role="img" aria-label="Dark tonal repeat pattern"></div>
  <div class="wordmark light">Brennick<span class="dot"></span></div>
</section>
<div class="coil cover"></div>

<section class="piece notebook-open">
  <div class="page left">
    <div class="wordmark">Brennick<span class="dot"></span></div>
    <div class="date-line">Date:....../....../......</div>
    <div class="lines"></div>
    <div class="band">27-310 Cedar Point Rd, Guelph, ON N1K 4T2</div>
  </div>
  <div class="page right">
    <div class="wordmark">Brennick<span class="dot"></span></div>
    <div class="date-line">Date:....../....../......</div>
    <div class="lines"></div>
    <div class="band">27-310 Cedar Point Rd, Guelph, ON N1K 4T2</div>
  </div>
  <div class="coil open"></div>
</section>

</body>
</html>
```